Business card design

Hi,
I need to have a business card design based on the current logo.
If competitive I not put it out to everyone.

It can be single of double sided

Target Market(s)

Food businesses

Industry/Entity Type

Food Manufacturing

Contact Information for Business Card

Details will on card will be as follows Name = Marcus Bell Email = Marcus@PanHearth.com.au Phone = 0418563207 Address = 57 Larkin Street , Fortitude Valley QLD 4006 Australia

Font styles to use
Other font styles liked:
• based on two fonts - Adelle & Museo

Requirements
Must have
• Based on the on switch concept

```html
<!DOCTYPE html>
<html lang="en">
<head>
<meta charset="utf-8">
<title>PanHearth Business Card</title>
<link href="https://fonts.googleapis.com/css2?family=Arimo:wght@400;700&family=Zilla+Slab:wght@500&display=swap" rel="stylesheet">
<style>
  :root {
    --bg: #dcdcdc;
    --cocoa: #3f2a2c;
    --cherry: #e8264a;
    --paper: #f4f4f4;
    --ink: #2a2a2a;
    --white: #ffffff;
  }
  * { margin: 0; padding: 0; box-sizing: border-box; }
  html, body {
    width: 1200px;
    height: 930px;
    overflow: hidden;
    background: var(--bg);
    font-family: "Arimo", Arial, sans-serif;
  }
  .canvas { position: relative; width: 1200px; height: 930px; }
  .card {
    position: absolute;
    width: 520px;
    height: 318px;
    box-shadow: 0 2px 6px rgba(0,0,0,0.12);
    overflow: hidden;
  }
  .card--brand {
    left: 600px; top: 110px;
    background: var(--cocoa);
    display: flex;
    align-items: center;
    justify-content: center;
  }
  .brand-lockup { display: flex; flex-direction: column; align-items: flex-end; }
  .brand-name {
    display: flex; align-items: center; gap: 14px;
    color: var(--white);
    font-weight: 700;
    font-size: 52px;
    letter-spacing: 3px;
    text-transform: uppercase;
  }
  .brand-dot {
    width: 40px; height: 40px; border-radius: 50%;
    background: var(--white);
  }
  .brand-tagline {
    font-family: "Zilla Slab", Georgia, serif;
    font-weight: 500;
    color: var(--white);
    font-size: 17px;
    letter-spacing: 1px;
    margin-top: 4px;
  }
  .card--contact {
    left: 80px; top: 480px;
    background: var(--paper);
    display: flex;
  }
  .contact-mark {
    width: 44%;
    background: var(--cocoa);
    display: flex; flex-direction: column;
    align-items: center; justify-content: center; gap: 14px;
  }
  .mark-dot { width: 54px; height: 54px; border-radius: 50%; background: var(--cherry); }
  .mark-name {
    color: var(--cherry);
    font-weight: 700;
    font-size: 28px;
    letter-spacing: 2px;
    text-transform: uppercase;
  }
  .contact-details { flex: 1; padding: 46px 0 0 34px; color: var(--ink); }
  .person-name {
    color: var(--cherry);
    font-weight: 700;
    font-size: 21px;
    letter-spacing: 1px;
    text-transform: uppercase;
    margin-bottom: 14px;
  }
  .address { font-size: 15px; line-height: 1.3; margin-bottom: 22px; }
  .contact-list { list-style: none; font-size: 15px; line-height: 1.45; }
  .contact-list li { display: flex; align-items: center; gap: 8px; }
  .contact-list svg { width: 13px; height: 13px; flex: none; fill: var(--cherry); }
</style>
</head>
<body>
<main class="canvas">
  <section class="card card--brand">
    <div class="brand-lockup">
      <div class="brand-name"><span class="brand-dot"></span>PanHearth</div>
      <div class="brand-tagline">Fresh Kitchen Supply Daily</div>
    </div>
  </section>

  <section class="card card--contact">
    <div class="contact-mark">
      <span class="mark-dot"></span>
      <span class="mark-name">PanHearth</span>
    </div>
    <div class="contact-details">
      <h1 class="person-name">Marcus Bell</h1>
      <p class="address">57 Larkin Street<br>Fortitude Valley<br>QLD 4006 Australia</p>
      <ul class="contact-list">
        <li><svg viewBox="0 0 16 16" aria-hidden="true"><path d="M3.5 1l3 3-1.8 1.8a9 9 0 0 0 5.5 5.5L12 9.5l3 3-2 2.5C6.5 14.5 1.5 9.5 1 3z"/></svg>0418563207</li>
        <li><svg viewBox="0 0 16 16" aria-hidden="true"><path d="M1 3h14v10H1z M1 3l7 6 7-6" /></svg>Marcus@PanHearth.com.au</li>
        <li><svg viewBox="0 0 16 16" aria-hidden="true"><circle cx="8" cy="8" r="7"/></svg>www.PanHearth.com.au</li>
      </ul>
    </div>
  </section>
</main>
</body>
</html>
```